Red Mesa Greenworks Summit needs a marketing flyer

We need a full page graphic for our upcoming Forum that can also be converted into a website "header" for social media, etc.: "Red Mesa Greenworks Summit - Shaping Change Across the Made Landscape"

INTRODUCTION:
During the first week of August 2022, Q-VarDT is presenting the Red Mesa Greenworks Summit - Shaping Change Across the Made Landscape.

One of the most exciting aspects of this conference will be the bringing together of multiple organizations including for-profits and nonprofits, K-12’s and higher education, cities and counties and other governmental agencies, as well as architects, engineers, and contractors to collaboratively present and discuss issues and ideas related to sustainability, with a Texas focus.

This event will be a catalyst for public and private project owners to holistically gather information and momentum as we bring the resources and vision needed to achieve the goal of zero carbon emissions from the built environment by 2040, and address water, green space and the natural environment, transportation, equity, and funding, among other topics.

```html
<!DOCTYPE html>
<html lang="en">
<head>
<meta charset="utf-8">
<title>Red Mesa Greenworks Summit – Flyer</title>
<link href="https://fonts.googleapis.com/css2?family=Montserrat:wght@400;500;600;700;800&family=Oswald:wght@500&display=swap" rel="stylesheet">
<style>
  :root {
    --backdrop: #b3b3b3;
    --paper: #ffffff;
    --leaf: #8cb03f;
    --leaf-soft: #97b548;
    --leaf-light: #c4dc6a;
    --leaf-deep: #5f8a2a;
    --navy: #31458e;
    --ink: #222222;
    --slate: #444444;
  }
  * { margin: 0; padding: 0; box-sizing: border-box; }
  html, body { width: 1047px; height: 1200px; overflow: hidden; }
  body {
    background: var(--backdrop);
    font-family: "Montserrat", sans-serif;
    position: relative;
  }
  .flyer {
    position: absolute;
    left: 184px; top: 165px;
    width: 693px; height: 895px;
    background: var(--paper);
  }
  .hero-art {
    position: absolute;
    left: 56px; top: 22px;
    width: 570px; height: 335px;
    border-radius: 285px 285px 40px 40px / 300px 300px 40px 40px;
    background: radial-gradient(circle at 50% 40%, var(--leaf-light) 0%, var(--leaf) 55%, var(--leaf-deep) 100%);
  }
  .event-name {
    position: absolute; left: 57px; top: 386px;
    font-size: 27px; font-weight: 500; color: var(--slate);
    letter-spacing: 0.2px;
  }
  .rule {
    position: absolute; left: 57px; top: 429px;
    width: 68px; height: 3px; background: var(--leaf);
  }
  .headline {
    position: absolute; left: 56px; top: 442px;
    color: var(--leaf); font-weight: 700; line-height: 1;
  }
  .headline .line-1 { display: block; font-size: 40px; letter-spacing: 0.5px; }
  .headline .line-2 { display: block; font-size: 23px; letter-spacing: 5.4px; margin-top: 8px; }
  .intro {
    position: absolute; left: 57px; top: 529px; width: 586px;
    font-size: 13.3px; line-height: 16.6px; color: var(--ink);
  }
  .pricing-band {
    position: absolute; left: 0; top: 623px;
    width: 693px; height: 175px; background: var(--navy);
  }
  .pricing-band h2 {
    position: absolute; left: 57px; top: 11px;
    font-size: 16.5px; font-weight: 700; color: var(--leaf-soft);
    letter-spacing: 0.2px;
  }
  .price-card {
    position: absolute; left: 57px; top: 43px;
    width: 583px; height: 105px; border-radius: 14px;
    background: var(--leaf-soft); color: #fff;
  }
  .tier {
    position: absolute; top: 11px; text-align: center;
  }
  .tier .label { font-size: 13px; font-weight: 700; letter-spacing: 0.2px; }
  .tier .price { font-family: "Oswald", sans-serif; font-size: 29px; font-weight: 500; margin-top: 6px; }
  .tier-members { left: 14px; width: 100px; }
  .tier-nonmember { left: 164px; width: 120px; }
  .tier-public { left: 330px; width: 230px; }
  .divider {
    position: absolute; top: 14px; height: 56px;
    border-left: 1px dotted rgba(255,255,255,0.7);
  }
  .divider-a { left: 140px; }
  .divider-b { left: 310px; }
  .offer {
    position: absolute; left: 0; right: 0; top: 80px;
    text-align: center; font-size: 14.5px; font-weight: 500;
  }
  .org-mark {
    position: absolute; left: 69px; top: 825px;
    display: flex; align-items: center; gap: 6px;
  }
  .org-mark .dot { width: 58px; height: 58px; border-radius: 50%; background: var(--navy); }
  .org-mark .name { font-size: 29px; font-weight: 600; color: var(--slate); }
  .contact {
    position: absolute; left: 416px; top: 835px;
    font-size: 13px; line-height: 21px; color: var(--ink);
  }
  .social {
    position: absolute; left: 548px; top: 853px;
    display: flex; gap: 22px;
  }
  .social span { width: 16px; height: 16px; border-radius: 50%; background: var(--navy); display: block; }
</style>
</head>
<body>
  <main class="flyer">
    <div class="hero-art" role="img" aria-label="Paper-cut green city skyline with clouds, sun, wind turbines, capitol dome, towers and trees"></div>

    <p class="event-name">Red Mesa Greenworks Summit</p>
    <div class="rule"></div>
    <h1 class="headline">
      <span class="line-1">SHAPING CHANGE</span>
      <span class="line-2">ACROSS THE MADE LANDSCAPE</span>
    </h1>
    <p class="intro">You may have added some new skills to your repertoire, or honed some old ones. You may see where our design and construction industry can make some improvements. There is a new energy in the air as we move beyond anxiety or fears that have blocked us or our organizations in the past. Now is the time to reinvent and evolve into a newer, better version of US.</p>

    <section class="pricing-band">
      <h2>JOIN US AT THE Q-VARDT INVEST IN WOMEN FORUM:</h2>
      <div class="price-card">
        <div class="tier tier-members"><div class="label">MEMBERS</div><div class="price">$175</div></div>
        <div class="divider divider-a"></div>
        <div class="tier tier-nonmember"><div class="label">NON-MEMBER</div><div class="price">$200</div></div>
        <div class="divider divider-b"></div>
        <div class="tier tier-public"><div class="label">GOVERNMENT /NON-PROFIT</div><div class="price">$125</div></div>
        <p class="offer">REGISTER 2, GET ONE FREE.</p>
      </div>
    </section>

    <div class="org-mark"><span class="dot"></span><span class="name">Q-VarDT</span></div>
    <div class="contact">555-014-2290<br>www.Q-VarDT.org</div>
    <div class="social" aria-label="Social links"><span></span><span></span><span></span></div>
  </main>
</body>
</html>
```